Black Car Limousine transportation business in Naples Florida

Always stand for my reliability and RVD stands for Love, K and M are the first initials of my children's names. It should show professionalism and a dedication to customer service. We keep our clients identities private. Show our professionalism. We are Black car Black tie company. We service transportation on a reserve basis to and from residents, airports, casinos, hotels,

Target Market(s)

It is a Private car service. High end clients. Businesses, Celebrity and athletes. Service to airports, hotels, special events.

Industry/Entity Type

Business

Contact Information for Business Card

A pearl metallic or Luster card. Standard business card size. Would like the name, Company email, show we take credit cards and phone number. Currently I don't have a website but will like to add later.

Logo Text

STEADFAST RVD TRANSPORTATION

Font styles to use
Serif

Colors
eaeaea
000000

Requirements
Must have
• Must have Company email, show we take credit cards and phone number. Currently I don't have a website but will like to add later.
Nice to have
• Would like to stay with a black and white theme. Open to some color trim.
Should not have
• Open to suggestions

```html
<!DOCTYPE html>
<html lang="en">
<head>
<meta charset="utf-8">
<title>Steadfast RVD Transportation – Business Card</title>
<link rel="stylesheet" href="https://fonts.googleapis.com/css2?family=PT+Serif:wght@400;700&display=swap">
<style>
  :root {
    --backdrop: #939393;
    --card-light: #f2f2f2;
    --card-dark: #333333;
    --ink-strong: #1f1f1f;
    --ink-soft: #555555;
    --ink-light: #ffffff;
    --vehicle-dark: #141414;
    --vehicle-mid: #3a3a3a;
  }
  * { box-sizing: border-box; margin: 0; padding: 0; }
  html, body {
    width: 1200px;
    height: 900px;
    overflow: hidden;
    background: var(--backdrop);
    font-family: "PT Serif", serif;
  }
  .stage { position: relative; width: 1200px; height: 900px; }
  .card {
    position: absolute;
    top: 185px;
    height: 489px;
    border-radius: 12px;
    box-shadow: 0 1px 3px rgba(0,0,0,0.18);
  }
  .card--front { left: 299px; width: 301px; background: var(--card-light); }
  .card--back  { left: 645px; width: 304px; background: var(--card-dark); }

  .wordmark {
    position: absolute;
    left: 0; right: 0;
    text-align: center;
    font-weight: 700;
    font-size: 24px;
    line-height: 1.25;
    letter-spacing: 0.5px;
  }
  .card--front .wordmark { top: 128px; color: var(--ink-strong); }
  .card--back .wordmark  { top: 118px; color: var(--ink-light); }

  .contact {
    position: absolute;
    top: 262px;
    left: 0; right: 0;
    text-align: center;
    color: var(--ink-soft);
    font-size: 13px;
    line-height: 17.5px;
  }
  .contact__name {
    font-size: 16px;
    font-weight: 700;
    color: var(--ink-strong);
    line-height: 20px;
  }
  .contact__role { margin-bottom: 11px; }
  .contact__address { margin-bottom: 13px; }

  .payment {
    display: flex;
    align-items: center;
    justify-content: center;
    gap: 6px;
    margin-top: 2px;
  }
  .payment__icon { width: 18px; height: 13px; }

  .vehicle-photo {
    position: absolute;
    left: 18px;
    top: 288px;
    width: 272px;
    height: 155px;
  }
</style>
</head>
<body>
<main class="stage">
  <section class="card card--front" aria-label="Card front">
    <div class="wordmark">STEADFAST RVD<br>TRANSPORTATION</div>
    <div class="contact">
      <p class="contact__name">Daniel Moreau</p>
      <p class="contact__role">Managing Director</p>
      <p class="contact__address">4810, Harbor Point Drive<br>Naples Florida, 34102.</p>
      <p class="contact__lines">044-555 010 203<br>info@rvdcars.com</p>
      <p class="payment">
        <svg class="payment__icon" viewBox="0 0 18 13" aria-hidden="true">
          <rect x="0.5" y="0.5" width="17" height="12" rx="2" fill="none" stroke="currentColor"/>
          <rect x="0.5" y="3" width="17" height="2.5" fill="currentColor"/>
          <rect x="3" y="8.5" width="5" height="1.5" fill="currentColor"/>
        </svg>
        <span>Major credit cards accepted</span>
      </p>
    </div>
  </section>

  <section class="card card--back" aria-label="Card back">
    <div class="wordmark">STEADFAST RVD<br>TRANSPORTATION</div>
    <svg class="vehicle-photo" viewBox="0 0 272 155" role="img" aria-label="Photo of a black luxury SUV">
      <defs>
        <radialGradient id="vehicleTone" cx="50%" cy="55%" r="60%">
          <stop offset="0%" stop-color="#3a3a3a"/>
          <stop offset="100%" stop-color="#141414"/>
        </radialGradient>
      </defs>
      <rect x="0" y="0" width="272" height="155" rx="18" fill="url(#vehicleTone)"/>
    </svg>
  </section>
</main>
</body>
</html>
```